One of a Kind Clean Business Card

We need to design a new business card template for our company. Our company designs and produced merchandising displays. You can see a sample of what we produce on our site www.qorvanexhibits.net. I have uploaded our logo in vector format, as well as a picture of our current business cards. We want a totally different look. We want simple and clean, looking forward to seeing what people create.
Updates

I would like to update the address for Qorvan Display Group Inc. 518 E Tollmere Ln Arlington Heights, IL 60017 Would also note. No QR codes

Industry/Entity Type

Business

Contact Information for Business Card

Need a 1 sided business card designed.

Font styles to use
Serif

Requirements
Must have
• Easy to view; Clean Design
Nice to have
• Features that promote engineering and creativity
Should not have
• Too much clutter, keep it simple

```html
<!DOCTYPE html>
<html lang="en">
<head>
<meta charset="utf-8">
<title>Qorvan Display Group Inc. – Business Card</title>
<link href="https://fonts.googleapis.com/css2?family=Open+Sans:wght@400;600&display=swap" rel="stylesheet">
<style>
  :root {
    --stage: #1f1f1f;
    --card: #fbfbf9;
    --band-light: #f3f3f3;
    --band-dark: #e2e2e2;
    --ink: #111111;
    --brand-red: #8a1420;
    --name-brown: #5a3510;
    --web-white: #ffffff;
    --rule: #1a1a1a;
    --pattern-tone: #e6e6e6;
  }
  * { box-sizing: border-box; margin: 0; padding: 0; }
  html, body {
    width: 1200px; height: 837px; overflow: hidden;
    background: var(--stage);
    font-family: "Open Sans", Arial, sans-serif;
  }
  .stage {
    width: 1200px; height: 837px;
    display: flex; align-items: center; justify-content: center;
  }
  .business-card {
    position: relative;
    width: 980px; height: 560px;
    background: var(--card);
    border-radius: 34px;
    overflow: hidden;
  }
  .brand {
    position: absolute; left: 70px; top: 64px;
    display: flex; align-items: center; gap: 16px;
  }
  .brand-mark {
    width: 22px; height: 22px; background: var(--brand-red);
  }
  .brand-name {
    font-size: 40px; font-weight: 400; color: var(--brand-red);
    letter-spacing: 1px;
  }
  .brand-rule {
    position: absolute; left: 70px; top: 130px;
    width: 560px; height: 3px; background: var(--rule);
  }
  .line-pattern {
    position: absolute; right: 70px; top: 60px;
    width: 260px; height: 200px;
    background: radial-gradient(ellipse at center, var(--pattern-tone), rgba(230,230,230,0) 70%);
  }
  .info-band {
    position: absolute; left: 0; right: 0; bottom: 0; height: 270px;
    background: linear-gradient(180deg, var(--band-light), var(--band-dark));
  }
  .person-name {
    position: absolute; left: 70px; top: 36px;
    font-size: 48px; font-weight: 400; color: var(--ink);
  }
  .person-name .surname { color: var(--name-brown); }
  .website {
    position: absolute; left: 70px; bottom: 34px;
    font-size: 22px; font-weight: 600; color: var(--web-white);
    letter-spacing: 3px;
    text-shadow: 0 0 2px rgba(0,0,0,0.15);
  }
  .contact-list {
    position: absolute; right: 60px; top: 96px;
    list-style: none; font-size: 20px; color: var(--ink);
    line-height: 1.45; text-align: right;
  }
  .contact-list b { font-weight: 600; }
</style>
</head>
<body>
<main class="stage">
  <article class="business-card">
    <div class="brand">
      <span class="brand-mark"></span>
      <span class="brand-name">Qorvan Display Group Inc.</span>
    </div>
    <div class="brand-rule"></div>
    <div class="line-pattern" role="img" aria-label="Faint engineering-style crossing line pattern"></div>
    <section class="info-band">
      <h1 class="person-name">Dale <span class="surname">Marrow</span></h1>
      <ul class="contact-list">
        <li><b>C:</b> 312-555-0147</li>
        <li><b>O:</b> 815-555-0192</li>
        <li><b>E:</b> dmarrow@qorvanexhibits.net</li>
        <li><b>L:</b> 518 E Tollmere Ln Arlington Heights, IL 60017</li>
      </ul>
      <p class="website">www.qorvanexhibits.net</p>
    </section>
  </article>
</main>
</body>
</html>
```